Velvet Riot Rising Line of Sparkling Wine & Spirits

Back info: Nora Beth Quill Owner 555-318-4402 1480 E. Harlow Ave, Bldg. 2, & 3, Lodi Ca. 95871
Sparkling Wines & Memorabilia www.velvetriotrising.com
Ok I have uploaded the winning design. The color that I am after is the Fushia, Raspberry, Red, Matte Satin Matalic Finish. With a 24 Karet Gold color Foil. The Bottle is on the top row and it's the 2nd Bottle in. That is the Color that I want. This is the style of font. Make sure that you put what we're advertising. Good Luck to you all. Warmest regards, Nora
21 & up UniSex
Sparkling Wine and Memorabilia
there listed up above.....

```html
<!DOCTYPE html>
<html lang="en">
<head>
<meta charset="utf-8">
<title>Velvet Riot Rising – Business Card</title>
<link rel="stylesheet" href="https://fonts.googleapis.com/css2?family=Arimo:wght@400;700&display=swap">
<style>
  :root {
    --page-bg: #e7e7e7;
    --card-white: #ffffff;
    --fuchsia: #c8166f;
    --fuchsia-bright: #e11a92;
    --fuchsia-deep: #8c1450;
    --gold: #a0762e;
    --ink: #4a4a4a;
    --rule: #555555;
    --logo-ink: #3b3b3b;
  }
  * { margin: 0; padding: 0; box-sizing: border-box; }
  html, body { width: 1200px; height: 1200px; overflow: hidden; }
  body {
    background: var(--page-bg);
    font-family: "Arimo", Arial, sans-serif;
    position: relative;
  }
  .card { position: absolute; width: 688px; height: 394px; }

  /* Front */
  .card-front { left: 267px; top: 158px; background: var(--card-white); }
  .bottle {
    position: absolute;
    border-radius: 10px 10px 8px 8px;
  }
  .card-front .bottle {
    left: 572px; top: 47px; width: 68px; height: 225px;
    background: linear-gradient(180deg, #5a1034 0%, #5a1034 28%, #c9a24a 29%, #c9a24a 32%, var(--fuchsia-bright) 33%, #c2106f 100%);
  }
  .owner-name {
    position: absolute; left: 49px; top: 283px;
    font-size: 25px; font-weight: 700; color: var(--fuchsia); letter-spacing: 0.2px;
  }
  .owner-role {
    position: absolute; left: 49px; top: 313px;
    font-size: 17px; color: var(--gold);
  }
  .owner-phone {
    position: absolute; left: 49px; top: 335px;
    font-size: 16.5px; color: var(--ink);
    display: flex; align-items: center; gap: 6px;
  }
  .owner-phone svg { width: 15px; height: 15px; }
  .divider {
    position: absolute; top: 287px; width: 1.5px; height: 73px; background: var(--rule);
  }
  .divider-a { left: 291px; }
  .divider-b { left: 436px; }
  .address {
    position: absolute; left: 306px; top: 290px;
    font-size: 16px; line-height: 20.5px; color: var(--ink); font-style: normal;
  }
  .web-list {
    position: absolute; left: 458px; top: 290px; list-style: none;
    font-size: 16px; line-height: 20.5px; color: var(--ink);
  }
  .web-list li { display: flex; align-items: center; gap: 6px; }
  .web-list svg { width: 14px; height: 14px; flex: none; }

  /* Back */
  .card-back {
    left: 262px; top: 653px; height: 393px; width: 687px;
    background: radial-gradient(ellipse 60% 70% at 52% 40%, var(--fuchsia-bright) 0%, #c4167e 45%, var(--fuchsia-deep) 100%);
  }
  .card-back .bottle {
    left: 102px; top: 65px; width: 75px; height: 257px;
    background: linear-gradient(180deg, #5a1034 0%, #5a1034 25%, #c9a24a 26%, #c9a24a 29%, #f02aa0 30%, #d0127a 100%);
  }
  .brand-name {
    position: absolute; left: 190px; top: 166px;
    font-size: 44px; font-weight: 700; color: var(--logo-ink); white-space: nowrap;
  }
  .brand-rule {
    position: absolute; left: 190px; top: 228px; width: 356px; height: 1px;
    background: rgba(80, 20, 50, 0.55);
  }
  .tagline {
    position: absolute; left: 192px; top: 238px;
    font-size: 17px; color: #ffffff; letter-spacing: 2px; white-space: nowrap;
  }
  .tagline strong { font-weight: 700; }
</style>
</head>
<body>

<section class="card card-front" aria-label="Business card front">
  <div class="bottle" role="img" aria-label="Illustration of a fuchsia sparkling wine bottle with gold foil collar"></div>

  <h1 class="owner-name">NORA BETH QUILL</h1>
  <p class="owner-role">Owner</p>
  <p class="owner-phone">
    <svg viewBox="0 0 24 24" aria-hidden="true"><path fill="#c8166f" d="M6.6 10.8a15.5 15.5 0 0 0 6.6 6.6l2.2-2.2a1 1 0 0 1 1-.25 11.4 11.4 0 0 0 3.6.57 1 1 0 0 1 1 1V20a1 1 0 0 1-1 1A17 17 0 0 1 3 4a1 1 0 0 1 1-1h3.5a1 1 0 0 1 1 1c0 1.25.2 2.45.57 3.57a1 1 0 0 1-.25 1z"/></svg>
    555-318-4402 1480
  </p>

  <span class="divider divider-a"></span>
  <address class="address">E. Harlow Ave<br>Bldg. 2, &amp; 3<br>Lodi Ca. 95871</address>

  <span class="divider divider-b"></span>
  <ul class="web-list">
    <li>
      <svg viewBox="0 0 24 24" aria-hidden="true"><circle cx="12" cy="12" r="10" fill="none" stroke="#c8166f" stroke-width="2.4"/><ellipse cx="12" cy="12" rx="4" ry="10" fill="none" stroke="#c8166f" stroke-width="2"/><line x1="2" y1="12" x2="22" y2="12" stroke="#c8166f" stroke-width="2"/></svg>
      velvetriotrising.com
    </li>
    <li>
      <svg viewBox="0 0 24 24" aria-hidden="true"><circle cx="12" cy="12" r="10" fill="#c8166f"/></svg>
      @velvetriotrising.com
    </li>
    <li>
      <svg viewBox="0 0 24 24" aria-hidden="true"><circle cx="12" cy="12" r="10" fill="#c8166f"/></svg>
      @velvetriotrising.com
    </li>
  </ul>
</section>

<section class="card card-back" aria-label="Business card back">
  <div class="bottle" role="img" aria-label="Illustration of a fuchsia sparkling wine bottle with gold foil collar"></div>
  <p class="brand-name">Velvet Riot Rising</p>
  <span class="brand-rule"></span>
  <p class="tagline">SPARKLING <strong>WINES &amp; MEMORABILIA</strong></p>
</section>

</body>
</html>
```